Stationery Design Project for Marketing Consultancy

I have started a new consultancy business and require the following elements to be designed using existing logo:
• Business card
• Letterhead
• Envelope (DL, C4, C5)
• Microsoft word template for report writing
• A4 Presentation Folder
• Powerpoint template
COPY FOR FRONT AND BACK OF BUSINESS CARD
logo
'Measurable Marketing. Epic Results' slogan (but no need to use existing lockup with logo)
name, B Bus. Mktg, Grad Dip Digital Mktg, CPM (post nominal abbreviations in smaller font)
mobile: 04XX-XXX-XXX (I will give details to the winner to add)
website: www.tolvarin.com.au
email: info@tolvarin.com.au
COPY FOR LETTERHEAD
Logo
Company Name
Please, submit your designs that include business card, letterhead and envelope. Once selected the winner will be asked to complete the project by creating the rest of the artwork.
FINAL FILES
Print ready files to be supplied as well as Indesign files so that minor amends can be made if necessary in future.
• Layered vectors in EPS & PDF
• Screen quality JPEG & PNGs
ABOUT THE BUSINESS: TOLVARIN
I work with clients to understand their business challenges, developing and executing measurable marketing strategies tied to key business metrics. Services include:
Services include:
• Business planning and business development
• Marketing and brand strategy
• Insight-driven integrated campaigns
• Loyalty programs and retention marketing
• Marketing automation
• Direct marketing (traditional and digital)
• Content strategy and development
Hi everyone,
Target Market(s)
Corporate decision makers (heads of marketing, general managers etc) and small to medium sized business owners. Predominately male aged 35+
Industry/Entity Type
Marketing
Requirements
Must have
- BRAND PERSONALITY
The successful design will communicate brand personality. I am a professional, results-driven entrepreneur, but want to show off my creative flair.
MEMORABILITY
Looking for a unique and eye-catching design. Am considering special printing effects (die cuts, letterpress, interactive elements, embossing, foiling etc) or a striking minimalist approach.
Nice to have
- I have a mission that could be incorporated on reverse if room -
Turning insights into actions & passion into profit.
Should not have
- Use of pink or green.

```html
<!DOCTYPE html>
<html lang="en">
<head>
<meta charset="utf-8">
<title>Tolvarin DL Envelope</title>
<link rel="stylesheet" href="https://fonts.googleapis.com/css2?family=Cabin:wght@600&family=Montserrat:wght@500&display=swap">
<style>
  :root {
    --backdrop: #d6d6d6;
    --slate: #2d3d47;
    --slate-deep: #1f2c33;
    --paper: #ffffff;
    --rule: #3a4a54;
    --band-text: #e8eef1;
  }
  html, body {
    margin: 0;
    padding: 0;
    width: 1200px;
    height: 901px;
    overflow: hidden;
    background: var(--backdrop);
  }
  .canvas {
    position: relative;
    width: 1200px;
    height: 901px;
  }
  .envelope-flap {
    position: absolute;
    left: 0;
    top: 0;
    width: 1200px;
    height: 901px;
  }
  .envelope-body {
    position: absolute;
    left: 113px;
    top: 283px;
    width: 977px;
    height: 489px;
    background: var(--paper);
    box-shadow: 0 2px 6px rgba(0,0,0,0.25);
  }
  .brand {
    position: absolute;
    left: 42px;
    top: 48px;
    display: flex;
    flex-direction: column;
    align-items: center;
    gap: 14px;
  }
  .brand-dot {
    width: 44px;
    height: 44px;
    border-radius: 50%;
    background: var(--slate);
  }
  .brand-name {
    font-family: "Cabin", sans-serif;
    font-weight: 600;
    font-size: 25px;
    letter-spacing: 1px;
    color: var(--slate);
  }
  .footer-rule {
    position: absolute;
    left: 0;
    right: 0;
    top: 444px;
    height: 2px;
    background: var(--rule);
  }
  .footer-band {
    position: absolute;
    left: 0;
    right: 0;
    bottom: 0;
    height: 37px;
    background: var(--slate);
    display: flex;
    align-items: center;
    justify-content: center;
  }
  .web-address {
    font-family: "Montserrat", sans-serif;
    font-weight: 500;
    font-size: 11px;
    color: var(--band-text);
  }
</style>
</head>
<body>
  <main class="canvas">
    <svg class="envelope-flap" viewBox="0 0 1200 901" aria-hidden="true">
      <defs>
        <linearGradient id="flapShade" x1="0" y1="0" x2="0" y2="1">
          <stop offset="0" stop-color="#2e3f49"/>
          <stop offset="1" stop-color="#1f2c33"/>
        </linearGradient>
      </defs>
      <path d="M113 283 L138 150 Q142 128 165 128 L1040 128 Q1062 128 1066 150 L1090 283 Z" fill="url(#flapShade)"/>
    </svg>
    <section class="envelope-body">
      <div class="brand">
        <div class="brand-dot"></div>
        <div class="brand-name">TOLVARIN</div>
      </div>
      <div class="footer-rule"></div>
      <div class="footer-band">
        <span class="web-address">www.tolvarin.com.au</span>
      </div>
    </section>
  </main>
</body>
</html>
```